Business Card for Fashion House

We need a business card design for our personalize fashion service for our customers. the business card should reflect reliability, luxury and creativity.
The brand Gravetto is extracted from "Graceful Velvetto"; Gravetto provides fashion designs sprinkled with luxury and style tailored for our elite clients character profile.
Gravetto is created for those who embody class and elegance with a passion for style.
Target Market(s)
Affluent Customers
Industry/Entity Type
Fashion
Contact Information for Business Card
Samira Haddadin
Fashion Designer
Telephone: +971 4 555 0192
Mobile +971 50 555 0147
Emal info@gravetto-example.com
Website www.gravetto-example.com
Social Media Youtube g+ Facebook Instagram Pin /gravetto
Font styles to use
Other font styles liked:
- Audrey provided
Look and feel
Each slider illustrates characteristics of the customer's brand and the style your logo design should communicate.

```html
<!DOCTYPE html>
<html lang="en">
<head>
<meta charset="utf-8">
<title>Gravetto Business Card</title>
<link href="https://fonts.googleapis.com/css2?family=Josefin+Sans:wght@400;600&display=swap" rel="stylesheet">
<style>
  :root {
    --backdrop: #d4d5d7;
    --card: #000000;
    --ink: #ffffff;
    --font: "Josefin Sans", sans-serif;
  }
  * { margin: 0; padding: 0; box-sizing: border-box; }
  html, body { width: 1200px; height: 1175px; overflow: hidden; }
  body {
    background: var(--backdrop);
    font-family: var(--font);
    color: var(--ink);
    position: relative;
  }
  .card {
    position: absolute;
    top: 442px;
    width: 535px;
    height: 305px;
    background: var(--card);
  }
  .card--front { left: 26px; }
  .card--back { left: 617px; }

  .brand-mark {
    position: absolute;
    left: 84px;
    top: 58px;
    font-size: 19px;
    letter-spacing: 0.12em;
    font-weight: 400;
  }
  .person { position: absolute; left: 42px; top: 142px; }
  .person__name { font-size: 17px; letter-spacing: 0.04em; font-weight: 400; }
  .person__role { font-size: 12.5px; margin-top: 3px; letter-spacing: 0.03em; }

  .contacts { position: absolute; left: 42px; top: 208px; list-style: none; }
  .contacts li {
    display: flex; align-items: center; gap: 8px;
    font-size: 13px; letter-spacing: 0.05em; height: 20px;
  }
  .contacts svg { width: 13px; height: 13px; flex: none; }
  .contacts .contacts__email { font-size: 11.5px; }

  .wordmark {
    position: absolute;
    right: 40px;
    top: 118px;
    font-size: 25px;
    letter-spacing: 0.42em;
    margin-right: -0.42em;
    font-weight: 400;
  }
  .social {
    position: absolute; right: 45px; top: 158px;
    display: flex; gap: 11px;
  }
  .social span { width: 20px; height: 20px; border-radius: 50%; background: var(--ink); }
  .website {
    position: absolute; right: 45px; top: 250px;
    font-size: 16px; letter-spacing: 0.12em; font-weight: 600;
  }
</style>
</head>
<body>
  <section class="card card--front">
    <div class="brand-mark">GRAVETTO</div>
    <div class="person">
      <p class="person__name">SAMIRA HADDADIN</p>
      <p class="person__role">Fashion Designer</p>
    </div>
    <ul class="contacts">
      <li>
        <svg viewBox="0 0 14 14" aria-hidden="true"><circle cx="7" cy="7" r="6.3" fill="none" stroke="#fff" stroke-width="1.2"/><path d="M4 5.2h6v4.4H4z" fill="#fff"/></svg>
        +971 50 555 0147
      </li>
      <li>
        <svg viewBox="0 0 14 14" aria-hidden="true"><circle cx="7" cy="7" r="6.3" fill="none" stroke="#fff" stroke-width="1.2"/><rect x="5" y="3.5" width="4" height="7" rx="0.8" fill="none" stroke="#fff" stroke-width="1"/></svg>
        +971 4 555 0192
      </li>
      <li class="contacts__email">
        <svg viewBox="0 0 14 14" aria-hidden="true"><circle cx="7" cy="7" r="6.3" fill="none" stroke="#fff" stroke-width="1.2"/><path d="M3.8 4.8h6.4v4.4H3.8z M3.8 4.8 7 7.4l3.2-2.6" fill="none" stroke="#fff" stroke-width="0.9"/></svg>
        info@gravetto-example.com
      </li>
    </ul>
  </section>

  <section class="card card--back">
    <div class="wordmark">GRAVETTO</div>
    <div class="social" aria-label="Social media /gravetto">
      <span></span><span></span><span></span><span></span><span></span><span></span>
    </div>
    <div class="website">www.gravetto-example.com</div>
  </section>
</body>
</html>
```